Front page on www.brightmarkgoods.com modern service ads - each ad for each featured service

We need to have initial 5 banners to be created for our soon to be launched new site,. These are 5 rotating banners that will showcase our companies key features. We are looking for a modern stylish yet simple look to highlight these features. Something thats very inviting and modern to fit the look of the new website.

5 banners need to be, information can be found on www.brightmarkgoods.com about these. Please ask if any questions

Why us?
Art Services
Order Process
Current promotions
Clearance products

please also note. the design will be going onto this website. http://new.brightmarkgoods.com/ Please base actual designs , color schemes etc.. for the new site.

Target Market(s)

Small businesses that purchase marketing promotional goods, to promote their business

Industry/Entity Type

Promotional Product

Font styles to use
Sans Serif

Requirements
Must have
• Size of the banner is 965 x 400 px
Nice to have
• Modern elements,, very clean and minimal look
Should not have
• no cheap generic clip art

```html
<!DOCTYPE html>
<html lang="en">
<head>
<meta charset="utf-8">
<title>Order Process – Brightmark Goods</title>
<link rel="stylesheet" href="https://fonts.googleapis.com/css2?family=Montserrat:wght@600;700;800&display=swap">
<style>
  :root {
    --navy: #282f5e;
    --lavender: #a4aee0;
    --lavender-deep: #8e98d7;
    --lavender-soft: #b6bde6;
    --lilac-light: #e2daf6;
    --white: #ffffff;
    --ink: #2a2e52;
  }
  html, body {
    margin: 0;
    padding: 0;
    width: 1200px;
    height: 497px;
    overflow: hidden;
    background: var(--lavender);
  }
  .banner {
    position: relative;
    width: 1200px;
    height: 497px;
    overflow: hidden;
    font-family: "Montserrat", Arial, sans-serif;
  }
  .stage {
    position: absolute;
    left: 0;
    top: 0;
    width: 965px;
    height: 400px;
    transform: scale(1.2435);
    transform-origin: 0 0;
  }
  .backdrop {
    position: absolute;
    inset: 0;
    width: 965px;
    height: 400px;
  }
  .site-url {
    position: absolute;
    left: 112px;
    top: 86px;
    margin: 0;
    font-size: 16.5px;
    font-weight: 700;
    color: var(--ink);
    letter-spacing: 0.2px;
  }
  .headline {
    margin: 0;
    position: absolute;
    left: 0;
    top: 0;
  }
  .headline-main {
    position: absolute;
    left: 64px;
    top: 112px;
    font-size: 104px;
    font-weight: 700;
    line-height: 1;
    color: var(--white);
    letter-spacing: -1.5px;
    white-space: nowrap;
  }
  .headline-sub {
    position: absolute;
    left: 103px;
    top: 230px;
    font-size: 62px;
    font-weight: 600;
    line-height: 1;
    color: var(--white);
    white-space: nowrap;
  }
  .features {
    position: absolute;
    left: 570px;
    top: 108px;
    margin: 0;
    padding: 0;
    list-style: none;
  }
  .feature {
    display: flex;
    align-items: flex-start;
    margin-bottom: 17px;
  }
  .feature-icon {
    width: 34px;
    height: 38px;
    flex: none;
    margin-right: 22px;
  }
  .feature-text {
    color: var(--white);
    font-size: 16.5px;
    font-weight: 700;
    line-height: 23px;
    text-transform: uppercase;
    padding-top: 4px;
  }
</style>
</head>
<body>
<div class="banner">
  <div class="stage">
    <svg class="backdrop" viewBox="0 0 965 400" aria-hidden="true">
      <defs>
        <linearGradient id="glow" x1="0" y1="0" x2="1" y2="0">
          <stop offset="0" stop-color="#ffffff" stop-opacity="0.55"/>
          <stop offset="1" stop-color="#ffffff" stop-opacity="0"/>
        </linearGradient>
        <filter id="blur" x="-20%" y="-200%" width="140%" height="500%">
          <feGaussianBlur stdDeviation="6"/>
        </filter>
      </defs>
      <rect width="965" height="400" fill="var(--lavender)"/>
      <polygon points="490,0 790,0 965,120 965,180 560,330" fill="var(--lavender-deep)" opacity="0.55"/>
      <polygon points="790,0 965,0 965,110" fill="var(--lilac-light)"/>
      <polygon points="700,0 790,0 965,110 965,150" fill="#c9c6ee" opacity="0.6"/>
      <polygon points="965,240 965,400 890,400" fill="var(--lavender-deep)" opacity="0.7"/>
      <polygon points="550,335 965,240 890,400 400,400" fill="var(--lavender-soft)" opacity="0.5"/>
      <polygon points="490,0 520,0 580,330 550,335" fill="url(#glow)"/>
      <polygon points="0,0 340,0 0,48" fill="var(--lavender-deep)"/>
      <polygon points="0,48 340,0 490,0 550,335 400,400 300,400 0,318" fill="var(--white)"/>
      <polygon points="0,318 300,400 0,400" fill="var(--navy)"/>
      <polygon points="45,112 472,106 472,226 58,240" fill="var(--navy)"/>
      <polygon points="93,233 425,228 425,300 95,305" fill="var(--lavender-deep)"/>
      <ellipse cx="265" cy="318" rx="150" ry="5" fill="#555" opacity="0.35" filter="url(#blur)"/>
    </svg>

    <p class="site-url">WWW.BRIGHTMARKGOODS.COM</p>

    <h1 class="headline">
      <span class="headline-main">ORDER</span>
      <span class="headline-sub">PROCESS</span>
    </h1>

    <ul class="features">
      <li class="feature">
        <svg class="feature-icon" viewBox="0 0 34 38" aria-hidden="true">
          <circle cx="17" cy="12" r="8" fill="#fff"/>
          <path d="M7 13 a10 10 0 0 1 20 0" fill="none" stroke="#fff" stroke-width="2.2"/>
          <rect x="5" y="11" width="4" height="7" rx="1.5" fill="#fff"/>
          <path d="M27 16 q0 6 -8 6" fill="none" stroke="#fff" stroke-width="1.8"/>
          <path d="M3 37 q1 -12 14 -13 q13 1 14 13 z" fill="#fff"/>
        </svg>
        <span class="feature-text">Easy order placement<br>(online &amp; offline)</span>
      </li>
      <li class="feature">
        <svg class="feature-icon" viewBox="0 0 34 38" aria-hidden="true">
          <path d="M17 2 a13 13 0 0 1 13 13 c0 9 -13 21 -13 21 s-13 -12 -13 -21 a13 13 0 0 1 13 -13 z" fill="#fff"/>
          <path d="M11 12 l6 -3 6 3 v7 l-6 3 -6 -3 z" fill="none" stroke="var(--lavender-deep)" stroke-width="1.6" stroke-linejoin="round"/>
          <path d="M11 12 l6 3 6 -3 M17 15 v7" fill="none" stroke="var(--lavender-deep)" stroke-width="1.6"/>
        </svg>
        <span class="feature-text">Full order tracking facility</span>
      </li>
      <li class="feature">
        <svg class="feature-icon" viewBox="0 0 34 38" aria-hidden="true">
          <rect x="3" y="6" width="28" height="28" rx="2" fill="none" stroke="#fff" stroke-width="2"/>
          <rect x="3" y="6" width="28" height="6" fill="#fff"/>
          <rect x="9" y="2" width="2.5" height="7" fill="#fff"/>
          <rect x="22.5" y="2" width="2.5" height="7" fill="#fff"/>
          <g fill="#fff">
            <rect x="7" y="15" width="4" height="3.5"/><rect x="13" y="15" width="4" height="3.5"/><rect x="19" y="15" width="4" height="3.5"/><rect x="25" y="15" width="3" height="3.5"/>
            <rect x="7" y="21" width="4" height="3.5"/><rect x="13" y="21" width="4" height="3.5"/><rect x="19" y="21" width="4" height="3.5"/><rect x="25" y="21" width="3" height="3.5"/>
            <rect x="7" y="27" width="4" height="3.5"/><rect x="13" y="27" width="4" height="3.5"/><rect x="19" y="27" width="4" height="3.5"/>
          </g>
        </svg>
        <span class="feature-text">Expedited shipping options<br>available</span>
      </li>
    </ul>
  </div>
</div>
</body>
</html>
```